Stationery for use with Ninefold Ridge reports

I would like to get a stationery design that my firm -- Ninefold Ridge Advisory -- will use as a format for reports that we send our clients. I am specifically looking for a design for use on a piece of paper or letterhead -- not business cards or envelopes.

We are an Africa based US risk intelligence and strategy firm that works with multinational corporations operating in West Africa. Our initial thinking is that we would like a color scheme consistent with our existing logo -- however we are open to other color schemes.

Also, we would like to see at least two separate versions: one with our company name and logo, the other without name and logo.

We also would like font recommendations for the stationary design.

The final design should communicate discreet professionalism and a modern approach, but it should not overshadow the words and information printed on the stationery.

Target Market(s)

Multinational corporations that currently use our products.

Font styles to use
Serif
Sans Serif

Requirements
Must have
• Sense of discreet professionalism that will not overshadow the content we put onto the stationery format.
• We would like to see designs with and without our company name/logo.
• Please suggest fonts that would work with the stationery.
Nice to have
• Ideally colors consistent with out existing logo, though we are open to and even encourage other ideas.
Should not have
• No need for business cards or envelopes.

```html
<!DOCTYPE html>
<html lang="en">
<head>
<meta charset="utf-8">
<title>Ninefold Ridge Advisory — Letterhead</title>
<link rel="stylesheet" href="https://fonts.googleapis.com/css2?family=Montserrat:wght@700&family=Roboto:wght@400&display=swap">
<style>
  :root {
    --backdrop: #d0ebf4;
    --paper: #ffffff;
    --ochre: #e0a84e;
    --sky: #acd7ef;
    --ink-navy: #1f3a4d;
    --ink-body: #5a5a5a;
    --ink-contact: #3d4f5c;
    --rule: #5b6b76;
  }
  html, body {
    margin: 0;
    padding: 0;
    width: 1200px;
    height: 1200px;
    overflow: hidden;
    background: var(--backdrop);
  }
  .letterhead {
    position: absolute;
    left: 242px;
    top: 94px;
    width: 716px;
    height: 1012px;
    background: var(--paper);
    font-family: "Roboto", Arial, sans-serif;
    color: var(--ink-body);
  }
  .header-wave {
    position: absolute;
    left: 0;
    top: 0;
    width: 716px;
    height: 100px;
  }
  .brand {
    position: absolute;
    left: 56px;
    top: 70px;
    width: 130px;
    text-align: center;
    font-family: "Montserrat", Arial, sans-serif;
    font-weight: 700;
    color: var(--ink-navy);
  }
  .brand-dot {
    display: block;
    width: 46px;
    height: 46px;
    margin: 0 auto 14px;
    border-radius: 50%;
    background: var(--ochre);
  }
  .brand-name {
    font-size: 19px;
    line-height: 22px;
    white-space: nowrap;
  }
  .brand-sub {
    font-size: 13px;
    letter-spacing: 2px;
    line-height: 18px;
  }
  .contact {
    position: absolute;
    left: 506px;
    top: 109px;
    height: 75px;
    border-left: 1.5px solid var(--rule);
    padding-left: 17px;
    font-size: 12.5px;
    line-height: 14.5px;
    color: var(--ink-contact);
  }
  .contact-address { margin-bottom: 7px; }
  .contact-line {
    display: flex;
    align-items: center;
    gap: 6px;
  }
  .contact-line svg { width: 9px; height: 9px; flex: none; }
  .contact-web .accent { color: var(--ochre); }
  .letter-date {
    position: absolute;
    left: 72px;
    top: 303px;
    font-size: 12.5px;
  }
  .letter-paragraph {
    position: absolute;
    left: 72px;
    margin: 0;
    font-size: 12.5px;
    line-height: 26px;
    white-space: nowrap;
  }
  .letter-paragraph span { display: block; }
  .signature-mark {
    position: absolute;
    left: 500px;
    top: 704px;
    width: 145px;
    height: 44px;
    background: linear-gradient(90deg, #f2f2f2, #e6e6e6);
    border-radius: 4px;
  }
  .signatory {
    position: absolute;
    left: 503px;
    top: 747px;
    font-size: 12.5px;
    line-height: 14.5px;
    color: var(--ink-contact);
  }
</style>
</head>
<body>
  <main class="letterhead">
    <svg class="header-wave" viewBox="0 0 716 100" aria-hidden="true">
      <path d="M0,0 H716 V88 C640,96 560,90 480,83 C330,52 150,20 0,48 Z" fill="var(--ochre)"/>
      <path d="M0,62 C150,36 330,58 480,84 C330,68 130,60 0,94 Z" fill="var(--sky)"/>
    </svg>

    <div class="brand">
      <span class="brand-dot"></span>
      <div class="brand-name">Ninefold Ridge</div>
      <div class="brand-sub">Advisory</div>
    </div>

    <address class="contact" style="font-style:normal">
      <div class="contact-address">Your address, city<br>state, ZIP 0000</div>
      <div class="contact-line">
        <svg viewBox="0 0 10 10"><path d="M2,0.5 L3.8,2.8 L2.8,4 C3.6,5.6 4.6,6.6 6,7.3 L7.2,6.3 L9.5,8 L8.4,9.5 C4.5,9 1,5.5 0.5,1.6 Z" fill="var(--ochre)"/></svg>
        <span>123-456-2100</span>
      </div>
      <div class="contact-line">
        <svg viewBox="0 0 10 10"><rect x="0.5" y="2" width="9" height="6.5" fill="var(--ochre)"/><path d="M0.5,2 L5,5.5 L9.5,2" stroke="#fff" stroke-width="1" fill="none"/></svg>
        <span>youremail@example.com</span>
      </div>
      <div class="contact-line contact-web">
        <svg viewBox="0 0 10 10"><circle cx="5" cy="5" r="4.5" fill="var(--ochre)"/><path d="M0.5,5 H9.5 M5,0.5 C2.5,3 2.5,7 5,9.5 M5,0.5 C7.5,3 7.5,7 5,9.5" stroke="#fff" stroke-width="0.8" fill="none"/></svg>
        <span>www.<span class="accent">yourwebsite</span>.com</span>
      </div>
    </address>

    <p class="letter-date">Date, 10 September, 2020</p>

    <p class="letter-paragraph" style="top:359px">
      <span>This is a sample letter that has been placed to demonstrate typing remat (Your Company). letterhead</span>
      <span>design. When positioned properly, it will serve to work in harmony with all other elements letterhead.</span>
      <span>This letterhead design is meant to project an image</span>
    </p>
    <p class="letter-paragraph" style="top:440px">
      <span>This letterhead design is meant project an image of professionalism reliability. By using simple aligen</span>
      <span>we have created a very spacious feeling. The simplicity suggest &nbsp;rengththe spaciousnes contributes h</span>
      <span>aesthetics the layout. These basic qualities along with the (Your Company)</span>
    </p>
    <p class="letter-paragraph" style="top:523px">
      <span>look and helps reinforce the (Your Company) brand. letterhead design is meant to project an image p</span>
      <span>design. When positioned properly, it will serve to work in harmony all the other elements letterhead.</span>
      <span>sionalism and reliability.</span>
    </p>
    <p class="letter-paragraph" style="top:610px">
      <span>This letterhead design is based on the (Form of your logo) form (Your Company) logo. Each stationery</span>
      <span>we have created a very spacious feeling. The simplicity suggests strength the spaciousnes contribute</span>
      <span>part of the (Form of your logo).</span>
    </p>

    <div class="signature-mark" role="img" aria-label="Handwritten signature of Ellis Marlowe"></div>
    <div class="signatory">Ellis Marlowe<br>Manager</div>
  </main>
</body>
</html>
```